Hartwell Estates Business Cards

I would like a business card that includes myself and my partner.
Includes: Logo, office #, email, website, our names, our numbers and possibly the address. I would also like the logo to be embossed and the card to be horizontal.
There is a photo of our yard signs to give you an idea of the colors of our business.

Target Market(s)

Everyone in real estate market.
We are in a rural area. Our clientele are from all socioeconomic backgrounds.

Industry/Entity Type

Real Estate Agent

Contact Information for Business Card

Company Name: Hartwell Estates
Our Names, Titles & Cell #'s : Dana Pembrook-Broker (555).317.6624, Marla Pembrook-Realtor (555).609.1385
Office #: (555).240.3918
Website: hartwellestates-demo.com
Joint Email: pembrook@hartwellestates-demo.com
Office Address: 418B W. Calloway Ave.
Larkmoor, KS. 70913

Font styles to use
Serif

Requirements
Must have
• HORIZONTAL, Logo, Myself and my partners names, Our cell #'s, our office #, our website, our email address
Nice to have
• Embossed logo, office address, our titles.

```html
<!DOCTYPE html>
<html lang="en">
<head>
<meta charset="utf-8">
<title>Hartwell Estates Business Cards</title>
<link rel="stylesheet" href="https://fonts.googleapis.com/css2?family=Tinos:wght@400;700&display=swap">
<style>
  :root {
    --brand-purple: #4a2265;
    --paper: #ffffff;
    --ink-grey: #4d4d4d;
    --backdrop: #e9e7e4;
    --card-shadow: rgba(40, 30, 50, 0.18);
  }
  * { box-sizing: border-box; margin: 0; padding: 0; }
  html, body {
    width: 1200px; height: 1189px; overflow: hidden;
    background: var(--backdrop);
    font-family: "Tinos", "Times New Roman", serif;
  }
  .sheet {
    width: 1200px; height: 1189px;
    display: flex; flex-direction: column; align-items: center; justify-content: center;
    gap: 52px;
  }
  .card {
    position: relative;
    width: 900px; height: 514px;
    box-shadow: 0 6px 22px var(--card-shadow);
    overflow: hidden;
  }

  /* Front */
  .card-front { background: var(--brand-purple); }
  .card-front .web-band {
    position: absolute; left: 0; right: 0; top: 370px; height: 80px;
    background: var(--paper);
    display: flex; align-items: center; justify-content: center;
  }
  .card-front .web-band span {
    color: var(--brand-purple); font-size: 22px; letter-spacing: 0.5px;
  }
  .card-front .wordmark {
    position: absolute; left: 0; right: 0; top: 150px;
    display: flex; align-items: center; justify-content: center; gap: 22px;
    color: var(--paper);
  }
  .wordmark .mark-square {
    width: 46px; height: 46px; border: 4px solid currentColor;
  }
  .wordmark .name {
    font-weight: 700; font-size: 58px; letter-spacing: 2px; line-height: 1;
  }

  /* Back */
  .card-back { background: var(--paper); }
  .card-back .wordmark {
    position: absolute; right: 56px; top: 60px;
    display: flex; flex-direction: column; align-items: flex-end; gap: 18px;
    color: var(--brand-purple);
  }
  .card-back .wordmark .mark-square { width: 120px; height: 120px; border-width: 14px; }
  .card-back .wordmark .name { font-size: 48px; }

  .agents { position: absolute; left: 0; top: 100px; }
  .agent { margin-bottom: 18px; }
  .agent-name {
    display: inline-block;
    background: var(--brand-purple); color: var(--paper);
    font-size: 30px; line-height: 34px;
    padding: 4px 40px 4px 44px; min-width: 320px;
  }
  .agent-partner { margin-left: 80px; }
  .agent-partner .agent-name { padding-left: 40px; }
  .agent-title, .agent-phone {
    padding-left: 74px; font-size: 20px; color: var(--ink-grey); line-height: 25px;
  }
  .agent-partner .agent-title, .agent-partner .agent-phone { padding-left: 70px; }
  .label { color: var(--brand-purple); font-weight: 700; }

  .office {
    position: absolute; left: 74px; top: 356px;
    font-style: normal;
    font-size: 20px; color: var(--ink-grey); line-height: 26px;
  }
</style>
</head>
<body>
<main class="sheet">
  <section class="card card-front" aria-label="Business card front">
    <div class="wordmark">
      <span class="mark-square" aria-hidden="true"></span>
      <span class="name">Hartwell Estates</span>
    </div>
    <div class="web-band"><span>hartwellestates-demo.com</span></div>
  </section>

  <section class="card card-back" aria-label="Business card back">
    <div class="wordmark">
      <span class="mark-square" aria-hidden="true"></span>
      <span class="name">Hartwell Estates</span>
    </div>

    <div class="agents">
      <div class="agent">
        <div class="agent-name">Dana Pembrook</div>
        <p class="agent-title">Broker</p>
        <p class="agent-phone"><span class="label">M:</span> (555).317.6624</p>
      </div>
      <div class="agent agent-partner">
        <div class="agent-name">Marla Pembrook</div>
        <p class="agent-title">Realtor</p>
        <p class="agent-phone"><span class="label">M:</span> (555).609.1385</p>
      </div>
    </div>

    <address class="office">
      <p><span class="label">Office:</span> (555).240.3918</p>
      <p><span class="label">Email:</span> pembrook@hartwellestates-demo.com</p>
      <p>418B W. Calloway Ave. Larkmoor, KS. 70913</p>
    </address>
  </section>
</main>
</body>
</html>
```